BrivoNest Learning App for Children with Dyslexia

Project Description:

We are seeking a talented UI/UX designer to create engaging and intuitive designs for Brivonest, an innovative educational app designed to help children learn letters and words through a multisensory learning approach. The app aims to be particularly helpful for children with dyslexia, providing a supportive and interactive learning environment.

Key App Features & Design Requirements:

Account Creation Screen: Design a welcoming and straightforward sign-up page that allows users to register with their email or continue with Quarnix. The design should be clean, focusing on user-friendliness and accessibility, adhering to our terms of service and privacy policy.

Main Screen Design: The main screen should allocate at least 4/6 of its height to the interactive drawing area. It needs to display word prompts in both correct and scrambled orders and include options to "Show all Words," "Play all words," and a search function. The interface should be vibrant, engaging, and easy to navigate for children.

Profile Section: Create a user-friendly profile page that allows users to edit their profile image, name, username, email, links, and bio. The design should be clean and encourage user engagement.

BrivoTally Page: This section will display the user's learning progress, including rankings, a learning curve, and recently learned words. It should visually represent progress in a motivating and understandable way, suitable for a younger audience.

Visual and Auditory Feedback Implementation: Incorporate elements that support visual and auditory feedback, using dyslexia-friendly formats. This includes choosing appropriate colors, fonts, and auditory cues.

Accessibility and Customization Settings: Designs should include settings for adjusting visual contrast, font size, and the word list to accommodate individual preferences and needs.

Feel free to add more interactions and/or pages.

Design preferences:

Color Scheme: Use a bright, inviting color palette that stimulates learning and engagement without overwhelming the users.
Font Selection: Opt for fonts that are readable and accessible, particularly for users with dyslexia.
Icons and Graphics: Design custom icons and graphics that are cohesive with the app's theme and purpose. Illustrations should be simple, relatable, and supportive of the learning process.

Target Market(s)

Educational

Industry/Entity Type

Educational

Colors
0054AA
0677BA
7BADD7
CADEEF
E8F1F8
0094D4
00A9DD
6FCCEA
C7EBF8
E9F6FB

Requirements
Must have
• Educational app, a writing area, scoring and account management
Nice to have
• Statistics, Ranking Page, Settings and some nice visual features

```html
<!DOCTYPE html>
<html lang="en">
<head>
<meta charset="utf-8">
<title>Brivonest – App Screens</title>
<link href="https://fonts.googleapis.com/css2?family=Ubuntu:wght@500;700&family=Roboto:wght@400;500;700&display=swap" rel="stylesheet">
<style>
:root{
  --stage:#a09c9d;
  --brand:#0a3fbf;
  --brand-deep:#0033a0;
  --brand-btn:#0a52b0;
  --brand-soft:#2c57bd;
  --ink:#141414;
  --muted:#6b6b6b;
  --lavender:#e3e8fb;
  --card:#f0f3fc;
  --card-line:#d7ddf0;
  --chip:#f1f2f6;
  --chip-active:#dbe6f8;
  --draw:#f4f4f4;
  --white:#ffffff;
}
*{box-sizing:border-box;margin:0;padding:0}
html,body{width:1200px;height:828px;overflow:hidden;background:var(--stage)}
body{position:relative;font-family:"Roboto",sans-serif}
.screen{position:absolute;top:62px;width:320px;height:692px;background:var(--white);overflow:hidden}
.screen--signup{left:66px;background:var(--lavender)}
.screen--main{left:444px}
.screen--profile{left:821px}
.abs{position:absolute}
.status-time{position:absolute;left:12px;top:8px;font:500 11px "Roboto",sans-serif;color:var(--white)}
.status-icons{position:absolute;right:14px;top:6px}
.header-shape{position:absolute;left:0;top:0}
/* signup */
.signup-title{position:absolute;left:0;width:320px;top:135px;text-align:center;font:700 27px "Ubuntu",sans-serif;color:var(--white)}
.logo-square{position:absolute;left:142px;top:67px;width:36px;height:36px;border-radius:7px;background:var(--white)}
.tagline{position:absolute;left:0;width:320px;top:191px;text-align:center;font:500 15px "Roboto",sans-serif;color:var(--white)}
.photo-ring{position:absolute;left:39px;top:205px;width:240px;height:240px;border-radius:50%;background:rgba(255,255,255,.07)}
.photo{position:absolute;left:53px;top:219px;width:212px;height:212px;border-radius:50%;background:radial-gradient(circle at 55% 60%,#e7b487 0%,#b9805a 35%,#5c6f86 75%,#2f4463 100%)}
.create-title{position:absolute;left:0;width:320px;top:474px;text-align:center;font:700 12px "Roboto",sans-serif;color:#0a3aa8;letter-spacing:.2px}
.email-input{position:absolute;left:34px;top:504px;width:252px;height:32px;border-radius:16px;background:var(--white);border:1px solid #cfd4e4;padding-left:13px;font:400 9.5px/30px "Roboto",sans-serif;color:#333}
.signup-btn{position:absolute;left:35px;top:545px;width:251px;height:31px;border-radius:16px;background:var(--brand-deep);color:var(--white);font:700 10px/31px "Roboto",sans-serif;text-align:center}
.terms{position:absolute;left:40px;width:240px;top:592px;text-align:center;font:400 9px/14.5px "Roboto",sans-serif;color:#666}
.divider-text{position:absolute;left:0;width:320px;top:630px;text-align:center;font:400 9px "Roboto",sans-serif;color:#0a3aa8}
.divider-line{position:absolute;top:636px;width:66px;height:1px;background:#0a3aa8}
.signup-footer{position:absolute;left:0;top:656px;width:320px;height:40px;background:var(--brand-deep);border-radius:20px 20px 0 0}
.alt-login{position:absolute;left:138px;top:648px;width:44px;height:44px;border-radius:50%;background:var(--white);font:700 9px/44px "Roboto",sans-serif;color:var(--brand-deep);text-align:center}
/* shared header */
.back-pill{position:absolute;left:243px;top:54px;width:66px;height:18px;border-radius:9px;border:1px solid rgba(255,255,255,.55);display:flex;align-items:center;justify-content:center;gap:8px;font:700 8.5px "Roboto",sans-serif;color:var(--white)}
.avatar{position:absolute;border-radius:50%;border:2px solid var(--white);background:radial-gradient(circle at 50% 40%,#e2b9a0 0%,#b07a5c 50%,#6b4a3a 100%)}
.user-name{position:absolute;left:53px;top:50px;font:700 9.5px "Roboto",sans-serif;color:var(--white)}
.user-mail{position:absolute;left:53px;top:64px;font:500 9.5px "Roboto",sans-serif;color:var(--white)}
.title-card{position:absolute;left:19px;top:132px;width:285px;height:51px;border-radius:26px;background:var(--card);border:1px solid var(--card-line)}
.title-card__text{position:absolute;top:11px;font:500 26px "Ubuntu",sans-serif;color:var(--ink);white-space:nowrap}
.title-card__text--profile{top:12px;font-size:24px}
.points{position:absolute;left:202px;top:13px;width:69px;height:24px;border-radius:12px;background:#0548a8;color:var(--white);font:500 10px/24px "Roboto",sans-serif;text-align:center}
.btn{position:absolute;top:200px;height:32px;border-radius:16px;font:400 10.5px/30px "Roboto",sans-serif;text-align:center}
.btn--outline{left:50px;width:107px;border:1px solid #5a5a5a;color:var(--ink);background:var(--white)}
.btn--solid{left:163px;width:107px;background:var(--brand-btn);color:var(--white);border:1px solid #0a3a90}
.chip{position:absolute;top:249px;width:77px;height:28px;border-radius:14px;background:var(--chip);color:#1849b0;font:400 10.5px/28px "Roboto",sans-serif;text-align:center}
.chip--active{background:var(--chip-active)}
.results-btn{position:absolute;left:22px;top:294px;width:275px;height:30px;border-radius:15px;background:var(--brand-btn);border:1px solid #083c8a;color:var(--white);font:500 10.5px/28px "Roboto",sans-serif;text-align:center}
.draw-area{position:absolute;left:12px;top:338px;width:297px;height:271px;border-radius:10px;background:var(--draw)}
.draw-area__title{position:absolute;left:3px;top:15px;font:700 19px "Ubuntu",sans-serif;color:#0a3fa8}
.edit-dot{position:absolute;width:28px;height:28px;border-radius:50%;background:var(--white);display:flex;align-items:center;justify-content:center}
/* nav */
.nav{position:absolute;left:0;top:633px;width:320px;height:59px;background:var(--brand-deep);border-radius:30px}
.nav__item{position:absolute;top:9px;width:38px;height:38px;border-radius:50%;background:var(--brand-soft);display:flex;align-items:center;justify-content:center}
.nav__item--active{background:var(--white)}
.nav__center{position:absolute;left:131px;top:611px;width:58px;height:58px;border-radius:50%;background:var(--white);border:3px solid #d9dce4;display:flex;align-items:center;justify-content:center}
.nav__center-inner{width:40px;height:40px;border-radius:50%;background:var(--brand-deep);display:flex;align-items:center;justify-content:center}
/* profile */
.brand-title{position:absolute;left:12px;top:47px;font:700 26px "Ubuntu",sans-serif;color:var(--white)}
.field-label{position:absolute;left:11px;display:flex;align-items:center;gap:3px;font:500 12.5px "Roboto",sans-serif;color:#0a3fa8}
.field-input{position:absolute;left:109px;width:191px;height:31px;border-radius:16px;border:1px solid #d9dce4;padding-left:17px;font:400 10.5px/29px "Roboto",sans-serif;color:#555}
.field-input svg{position:absolute;right:10px;top:10px}
.link-text{position:absolute;font:400 12px "Roboto",sans-serif;color:var(--ink)}
.add-link{position:absolute;left:237px;top:367px;width:26px;height:26px;border-radius:50%;background:#0a52b0;display:flex;align-items:center;justify-content:center}
.bio-box{position:absolute;left:7px;top:402px;width:306px;height:200px;border-radius:14px;border:1px solid #e1e4ec}
.bio-title{position:absolute;left:18px;top:8px;display:flex;align-items:center;gap:4px;font:500 12.5px "Roboto",sans-serif;color:#0a3fa8}
.bio-text{position:absolute;left:24px;top:35px;font:400 10.5px "Roboto",sans-serif;color:#555}
</style>
</head>
<body>
<svg width="0" height="0" style="position:absolute">
  <defs>
    <symbol id="i-status" viewBox="0 0 50 12">
      <rect x="0" y="8" width="2" height="4" fill="#fff"/><rect x="3" y="6" width="2" height="6" fill="#fff"/><rect x="6" y="4" width="2" height="8" fill="#fff"/><rect x="9" y="2" width="2" height="10" fill="#fff"/>
      <path d="M15 5 a7 7 0 0 1 10 0 M17 7.5 a4 4 0 0 1 6 0" stroke="#fff" stroke-width="1.4" fill="none"/><circle cx="20" cy="10" r="1.2" fill="#fff"/>
      <rect x="29" y="1.5" width="18" height="9" rx="2.5" stroke="#fff" stroke-width="1.2" fill="none"/><rect x="31" y="3.5" width="14" height="5" rx="1" fill="#fff"/><rect x="47.5" y="4.5" width="1.5" height="3" fill="#fff"/>
    </symbol>
    <symbol id="i-home" viewBox="0 0 12 12"><path d="M6 1.5 L11 6 H9.5 V10.5 H7.2 V7.5 H4.8 V10.5 H2.5 V6 H1 Z"/></symbol>
    <symbol id="i-bars" viewBox="0 0 16 16"><rect x="1" y="7" width="4" height="8"/><rect x="6" y="2" width="4" height="13"/><rect x="11" y="9" width="4" height="6"/></symbol>
    <symbol id="i-trophy" viewBox="0 0 16 16"><path d="M4 1 H12 V6 A4 4 0 0 1 4 6 Z"/><path d="M4 3 H1.5 V5 A3 3 0 0 0 4.5 8 M12 3 H14.5 V5 A3 3 0 0 1 11.5 8" stroke="currentColor" stroke-width="1.3" fill="none"/><rect x="7" y="9.5" width="2" height="3"/><rect x="4.5" y="12.5" width="7" height="2.5" rx=".6"/></symbol>
    <symbol id="i-gear" viewBox="0 0 16 16"><path d="M6.8 0.8 H9.2 L9.6 2.7 L11.2 3.4 L12.8 2.3 L14.5 4 L13.4 5.6 L14.1 7.2 L16 7.6 V9.9 L14.1 10.3 L13.4 11.9 L14.5 13.5 L12.8 15.2 L11.2 14.1 L9.6 14.8 L9.2 16.7 H6.8 L6.4 14.8 L4.8 14.1 L3.2 15.2 L1.5 13.5 L2.6 11.9 L1.9 10.3 L0 9.9 V7.6 L1.9 7.2 L2.6 5.6 L1.5 4 L3.2 2.3 L4.8 3.4 L6.4 2.7 Z M8 5.8 A2.9 2.9 0 1 0 8.001 5.8 Z" fill-rule="evenodd" transform="scale(1 .93)"/></symbol>
    <symbol id="i-badge" viewBox="0 0 18 18"><path d="M2 1.5 H16 V12.5 L9 16.5 L2 12.5 Z" fill="#fff"/><path d="M9 4 L10.3 6.8 L13.3 7.1 L11 9.1 L11.7 12 L9 10.5 L6.3 12 L7 9.1 L4.7 7.1 L7.7 6.8 Z" fill="#0033a0"/></symbol>
    <symbol id="i-edit" viewBox="0 0 12 12"><path d="M9 1.5 H1.5 V10.5 H10.5 V6" stroke="currentColor" stroke-width="1.1" fill="none"/><path d="M10 1 L11 2 L6 7 L4.7 7.3 L5 6 Z" fill="currentColor"/></symbol>
    <symbol id="i-user" viewBox="0 0 12 12"><circle cx="6" cy="3.5" r="2.6"/><path d="M1 11.5 C1 7.5 11 7.5 11 11.5 Z"/></symbol>
    <symbol id="i-mail" viewBox="0 0 14 11"><rect x="0.5" y="0.5" width="13" height="10" rx="1"/><path d="M1 1.5 L7 6 L13 1.5" stroke="#fff" stroke-width="1.2" fill="none"/></symbol>
    <symbol id="i-link" viewBox="0 0 14 14"><path d="M6 8 L8 6 M5.2 5.4 L3 7.6 A2.4 2.4 0 0 0 6.4 11 L8.6 8.8 M8.8 8.6 L11 6.4 A2.4 2.4 0 0 0 7.6 3 L5.4 5.2" stroke="currentColor" stroke-width="1.3" fill="none" stroke-linecap="round"/></symbol>
    <symbol id="i-cap" viewBox="0 0 16 12"><path d="M8 1 L16 4.5 L8 8 L0 4.5 Z"/><path d="M3.5 6.5 V9.5 C5.5 11.5 10.5 11.5 12.5 9.5 V6.5 L8 8.5 Z"/><rect x="14" y="4.5" width="1" height="5"/></symbol>
    <symbol id="i-back" viewBox="0 0 20 8"><path d="M19 4 H2 M5 1 L2 4 L5 7" stroke="#fff" stroke-width="1" fill="none"/></symbol>
  </defs>
</svg>

<!-- Account creation -->
<section class="screen screen--signup" aria-label="Create account screen">
  <svg class="header-shape" width="320" height="460" viewBox="0 0 320 460">
    <path d="M0 0 H320 V371 C300 420 240 453 160 453 C80 453 20 420 0 379 Z" fill="var(--brand)"/>
    <path d="M250 0 H320 V300 C300 260 270 230 250 200 Z" fill="#0939b3" opacity=".6"/>
  </svg>
  <div class="status-time">10.40</div>
  <svg class="status-icons" width="50" height="12"><use href="#i-status"/></svg>
  <div class="logo-square"></div>
  <div class="signup-title">Brivonest</div>
  <div class="tagline">Learn letters and words</div>
  <div class="photo-ring"></div>
  <div class="photo" role="img" aria-label="Photo of a young child drawing with a red pencil at a classroom table"></div>
  <div class="create-title">CREATE AN ACCOUNT</div>
  <div class="email-input">email@mailbox.test</div>
  <div class="signup-btn">SIGN UP WITH EMAIL</div>
  <p class="terms">By clicking continue, you agree to our and Terms of Service Privacy Policy</p>
  <div class="divider-line" style="left:47px"></div>
  <div class="divider-text">or continue with</div>
  <div class="divider-line" style="left:207px"></div>
  <div class="signup-footer"></div>
  <div class="alt-login">Quarnix</div>
</section>

<!-- Main screen -->
<section class="screen screen--main" aria-label="Main screen">
  <svg class="header-shape" width="320" height="130" viewBox="0 0 320 130">
    <path d="M0 0 H320 V88 Q160 125 0 92 Z" fill="var(--brand)"/>
  </svg>
  <div class="status-time">10.40</div>
  <svg class="status-icons" width="50" height="12"><use href="#i-status"/></svg>
  <div class="avatar" role="img" aria-label="User profile photo" style="left:11px;top:44px;width:34px;height:34px"></div>
  <div class="user-name">Tessa Marlow</div>
  <div class="user-mail">name@mailbox.test</div>
  <div class="back-pill"><svg width="18" height="8"><use href="#i-back"/></svg>Back</div>
  <div class="title-card">
    <span class="title-card__text" style="left:19px">Main Screen</span>
    <span class="points">16 points</span>
  </div>
  <div class="btn btn--outline">Show all Words</div>
  <div class="btn btn--solid">Play all Words</div>
  <div class="chip chip--active" style="left:12px">Word 1</div>
  <div class="chip" style="left:93px">Word 2</div>
  <div class="chip" style="left:174px">Word 3</div>
  <div class="chip" style="left:255px">Word 4</div>
  <div class="results-btn">Show me the results</div>
  <div class="draw-area">
    <h2 class="draw-area__title">Drawing Area</h2>
    <div class="edit-dot" style="left:246px;top:18px;color:#7a8fb8"><svg width="10" height="10"><use href="#i-edit"/></svg></div>
  </div>
  <nav class="nav">
    <div class="nav__item nav__item--active" style="left:19px"><svg width="13" height="13" fill="var(--brand-deep)"><use href="#i-home"/></svg></div>
    <div class="nav__item" style="left:80px"><svg width="18" height="18" fill="#fff"><use href="#i-bars"/></svg></div>
    <div class="nav__item" style="left:202px;color:#fff"><svg width="18" height="18" fill="#fff"><use href="#i-trophy"/></svg></div>
    <div class="nav__item" style="left:263px"><svg width="18" height="18" fill="#fff"><use href="#i-gear"/></svg></div>
  </nav>
  <div class="nav__center"><div class="nav__center-inner"><svg width="20" height="20"><use href="#i-badge"/></svg></div></div>
</section>

<!-- Profile -->
<section class="screen screen--profile" aria-label="Edit profile screen">
  <svg class="header-shape" width="320" height="130" viewBox="0 0 320 130">
    <path d="M0 0 H320 V88 Q160 125 0 92 Z" fill="var(--brand)"/>
  </svg>
  <div class="status-time">10.40</div>
  <svg class="status-icons" width="50" height="12"><use href="#i-status"/></svg>
  <div class="brand-title">Brivonest</div>
  <div class="back-pill"><svg width="18" height="8"><use href="#i-back"/></svg>Back</div>
  <div class="title-card">
    <span class="title-card__text title-card__text--profile" style="left:15px">Edit profile image</span>
    <div class="avatar" role="img" aria-label="User profile photo" style="left:241px;top:8px;width:33px;height:33px"></div>
  </div>

  <div class="field-label" style="top:214px"><svg width="10" height="10" fill="#0a3fa8"><use href="#i-user"/></svg>Name</div>
  <div class="field-input" style="top:207px">Tessa Marlow<svg width="11" height="11" style="color:#555"><use href="#i-edit"/></svg></div>

  <div class="field-label" style="top:256px"><svg width="10" height="10" fill="#0a3fa8"><use href="#i-user"/></svg>Username</div>
  <div class="field-input" style="top:248px">Tessa Marlow 0898<svg width="11" height="11" style="color:#555"><use href="#i-edit"/></svg></div>

  <div class="field-label" style="top:298px"><svg width="12" height="10" fill="#0a3fa8"><use href="#i-mail"/></svg>Email</div>
  <div class="field-input" style="top:291px">name@mailbox.test<svg width="11" height="11" style="color:#555"><use href="#i-edit"/></svg></div>

  <div class="field-label" style="top:340px"><svg width="13" height="13" style="color:#0a3fa8"><use href="#i-link"/></svg>Links</div>
  <span class="link-text" style="left:132px;top:340px">website.test</span>
  <span class="link-text" style="left:221px;top:340px">mylink.test</span>
  <span class="link-text" style="left:132px;top:364px">yourlink.test</span>
  <div class="add-link"><svg width="14" height="14"><path d="M7 1 V13 M1 7 H13" stroke="#fff" stroke-width="1.4"/></svg></div>

  <div class="bio-box">
    <div class="bio-title"><svg width="15" height="11" fill="#0a3fa8"><use href="#i-cap"/></svg>Bio</div>
    <svg width="11" height="11" class="abs" style="left:283px;top:12px;color:#555"><use href="#i-edit"/></svg>
    <p class="bio-text">A description of this user.</p>
  </div>

  <nav class="nav">
    <div class="nav__item" style="left:19px"><svg width="13" height="13" fill="#fff"><use href="#i-home"/></svg></div>
    <div class="nav__item" style="left:80px"><svg width="18" height="18" fill="#fff"><use href="#i-bars"/></svg></div>
    <div class="nav__item" style="left:202px;color:#fff"><svg width="18" height="18" fill="#fff"><use href="#i-trophy"/></svg></div>
    <div class="nav__item nav__item--active" style="left:263px"><svg width="19" height="19" fill="var(--brand-deep)"><use href="#i-gear"/></svg></div>
  </nav>
  <div class="nav__center"><div class="nav__center-inner"><svg width="20" height="20"><use href="#i-badge"/></svg></div></div>
</section>
</body>
</html>
```